Business Card Design for company

We want new business cards. We'd like something different-- yet still highly professional. Our tagline is Providing leadership, delivering success. Stock photos are ok, as long as they are relevant and look upscale.

Target Market(s)

Architecture/Business Management Consulting/Engineering Consulting

Contact Information for Business Card

dark gray background with pops of blue might be good, but you tell me. You're the designers. Rounded corners might be nice, but again, you tell me.

Font styles to use
Serif
Sans Serif

Colors
3276b5
5c5c5c
9d9d9d
fbfbfb

Requirements
Nice to have
• Something different, but still very professional.

```html
<!DOCTYPE html>
<html lang="en">
<head>
<meta charset="utf-8">
<title>Norvale Partners — Business Cards</title>
<link href="https://fonts.googleapis.com/css2?family=Montserrat:wght@600&family=Open+Sans:wght@400;600&display=swap" rel="stylesheet">
<style>
  :root {
    --scene: #2b292a;
    --card: #6a6a6a;
    --card-edge: #5c5c5c;
    --brand-blue: #3276b5;
    --ink-dark: #2e2e30;
    --text-light: #fbfbfb;
    --muted: #9d9d9d;
  }
  html, body {
    margin: 0;
    width: 1200px;
    height: 895px;
    overflow: hidden;
    background: var(--scene);
    font-family: "Open Sans", Arial, sans-serif;
  }
  .canvas {
    position: relative;
    width: 1200px;
    height: 895px;
  }
  .card {
    position: absolute;
    width: 600px;
    height: 343px;
    border-radius: 22px;
    background:
      repeating-linear-gradient(0deg, rgba(255,255,255,0.025) 0 1px, rgba(0,0,0,0.025) 1px 3px),
      linear-gradient(135deg, #727272, var(--card) 55%, var(--card-edge));
    box-shadow: 0 14px 30px rgba(0,0,0,0.45);
    overflow: hidden;
  }
  .card--front { left: 90px; top: 70px; }
  .card--back { left: 510px; top: 470px; }

  .world-backdrop {
    position: absolute;
    left: 40px; top: 40px;
    width: 520px; height: 230px;
    border-radius: 40%;
    background: radial-gradient(ellipse at center, rgba(90,90,90,0.55), rgba(106,106,106,0) 70%);
  }
  .front-wordmark {
    position: absolute;
    left: 0; right: 0; top: 120px;
    text-align: center;
    font-family: "Montserrat", Arial, sans-serif;
    font-weight: 600;
    font-size: 44px;
    letter-spacing: 2px;
    color: var(--ink-dark);
  }
  .front-url {
    position: absolute;
    left: 0; right: 0; top: 240px;
    text-align: center;
    font-size: 15px;
    letter-spacing: 3px;
    color: var(--ink-dark);
  }

  .back-wordmark {
    position: absolute;
    left: 36px; top: 148px;
    font-family: "Montserrat", Arial, sans-serif;
    font-weight: 600;
    font-size: 30px;
    line-height: 1.1;
    color: var(--brand-blue);
  }
  .divider {
    position: absolute;
    left: 300px; top: 50px;
    width: 2px; height: 243px;
    background: var(--text-light);
  }
  .contact {
    position: absolute;
    left: 326px; top: 58px;
    color: var(--text-light);
    font-size: 13.5px;
    line-height: 1.45;
  }
  .contact__name {
    margin: 0;
    font-family: "Montserrat", Arial, sans-serif;
    font-weight: 600;
    font-size: 22px;
    color: var(--brand-blue);
    letter-spacing: 0.5px;
  }
  .contact__title { margin: 0 0 12px; }
  .contact__address { margin: 0 0 12px; }
  .contact__list { list-style: none; margin: 0; padding: 0; }
  .contact__list li { display: flex; align-items: center; gap: 8px; }
  .contact__list svg { width: 12px; height: 12px; fill: var(--brand-blue); flex: none; }
</style>
</head>
<body>
<main class="canvas">

  <section class="card card--front" aria-label="Card front">
    <div class="world-backdrop" role="img" aria-label="Faint world map texture behind the company name"></div>
    <div class="front-wordmark">NORVALE PARTNERS</div>
    <div class="front-url">www.norvalepartners.com</div>
  </section>

  <section class="card card--back" aria-label="Card back">
    <div class="back-wordmark">NORVALE<br>PARTNERS</div>
    <div class="divider"></div>
    <div class="contact">
      <p class="contact__name">DANIEL REEVE</p>
      <p class="contact__title">Director</p>
      <p class="contact__address">48 Harrow Crescent, Suite 5<br>Leeds, United Kingdom LS1 4BX</p>
      <ul class="contact__list">
        <li>
          <svg viewBox="0 0 24 24" aria-hidden="true"><path d="M6.6 10.8a15 15 0 0 0 6.6 6.6l2.2-2.2c.3-.3.7-.4 1-.2 1.1.4 2.3.6 3.6.6.6 0 1 .4 1 1V20c0 .6-.4 1-1 1A17 17 0 0 1 3 4c0-.6.4-1 1-1h3.5c.6 0 1 .4 1 1 0 1.2.2 2.4.6 3.6.1.3 0 .7-.2 1z"/></svg>
          0113 496 0275
        </li>
        <li>
          <svg viewBox="0 0 24 24" aria-hidden="true"><path d="M2 5h20v14H2z M2 5l10 8 10-8" /></svg>
          d.reeve@norvalepartners.co.uk
        </li>
        <li>
          <svg viewBox="0 0 24 24" aria-hidden="true"><circle cx="12" cy="12" r="11"/></svg>
          www.norvalepartners.co.uk
        </li>
      </ul>
    </div>
  </section>

</main>
</body>
</html>
```